App Design - Career Prep Pal

We require an App Design for our new App called 'Hiring Helper'. This app is essentially an assistant to help Users prepare for job interviews, to help them get hired. <br/><br/>Users who download the App can view common Questions and Answers, save their favourite responses and also view common Interview Tips. <br/><br/>The vision for our App is for Users who are preparing for an interview (1 week before, 1 day before, even 1 hour before), are able to download, view and educate themselves on common questions and responses, and then be confident to land the job. <br/><br/>Our team has developed wireframes to help highlight what each screen should do and include. Please see attached document, which also highlights key requirements for the experience. Feel free to add/remove/edit what you see on these wireframes. Our preference is that you use Adobe XD please.<br/><br/>In terms of design guidelines, we want the experience to be simple, intuitive and 'memorable' to help Users to remember the questions/responses when they are in the interview. <br/><br/>The final design should communicate 'neat and clean professionalism'; we like the design of: jobvista net au<br/><br/>Thank you for reading! Good luck !

Target Market(s)

Professional job seekers

Font styles to use
Sans Serif

Colors

Designer to choose colors to be used in the design.

Requirements
Must have
• Please see my PixelGuild_UX file that I have uploaded
Nice to have
• Could you also please include some ideas on how we can incorporate Advertising into the app screens

```html
<!DOCTYPE html>
<html lang="en">
<head>
<meta charset="utf-8">
<title>Hiring Helper – App Screens</title>
<link href="https://fonts.googleapis.com/css2?family=Nunito:ital,wght@0,400;0,600;0,800;0,900;1,900&display=swap" rel="stylesheet">
<style>
  :root {
    --page-bg: #dde1ee;
    --brand-blue: #1448c4;
    --brand-blue-deep: #0c35a0;
    --brand-blue-soft: #3a6be0;
    --screen-bg: #f3f3f5;
    --card-bg: #ffffff;
    --ink: #111318;
    --ink-soft: #4a4d57;
    --white: #ffffff;
  }
  * { box-sizing: border-box; margin: 0; padding: 0; }
  html, body { width: 1200px; height: 900px; overflow: hidden; }
  body {
    background: var(--page-bg);
    font-family: "Nunito", "Helvetica Neue", Arial, sans-serif;
    color: var(--ink);
  }
  .screen-row {
    display: flex;
    gap: 32px;
    padding: 168px 32px 0;
  }
  .screen {
    position: relative;
    width: 260px;
    height: 564px;
    border-radius: 30px;
    background: var(--screen-bg);
    overflow: hidden;
    box-shadow: 0 18px 40px rgba(40, 52, 100, 0.18);
  }
  .app-header {
    position: absolute;
    left: 0; top: 0; width: 100%;
    background: linear-gradient(135deg, var(--brand-blue-soft) 0%, var(--brand-blue) 45%, var(--brand-blue-deep) 100%);
    color: var(--white);
  }
  .status-bar {
    position: absolute;
    top: 12px; left: 22px; right: 20px;
    display: flex; justify-content: space-between; align-items: center;
    font-size: 10px; font-weight: 800;
  }
  .status-icons { display: flex; gap: 4px; align-items: flex-end; }
  .app-title {
    position: absolute; left: 0; right: 0;
    text-align: center;
    font-size: 15px; font-weight: 900; font-style: italic;
    letter-spacing: 0.6px; text-transform: uppercase;
    white-space: nowrap;
  }
  .back-arrow { position: absolute; left: 14px; }
  .card {
    background: var(--card-bg);
    border-radius: 4px;
    box-shadow: 0 4px 14px rgba(20, 30, 60, 0.08);
  }

  /* Screen 1 – about */
  .about .app-header { height: 200px; }
  .about .app-title { top: 78px; }
  .about-card {
    position: absolute; left: 14px; right: 14px; top: 150px;
    padding: 26px 18px 24px;
    text-align: center;
  }
  .about-card h2 { font-size: 14px; font-weight: 900; font-style: italic; letter-spacing: 0.4px; margin-bottom: 40px; }
  .about-card p { font-size: 8.5px; line-height: 1.55; color: var(--ink-soft); text-align: left; }

  /* Screen 2 – home menu */
  .home .app-header { height: 190px; }
  .home .app-title { top: 68px; }
  .menu-list { position: absolute; left: 16px; right: 16px; top: 112px; display: flex; flex-direction: column; gap: 12px; }
  .menu-item {
    height: 132px;
    display: flex; flex-direction: column; align-items: center; justify-content: center; gap: 12px;
    font-size: 12.5px; font-weight: 600; letter-spacing: 0.3px;
  }

  /* Shared header for the question screens */
  .categories .app-header { height: 118px; }
  .categories .app-title, .questions .app-title {
    top: 62px; left: 32px; right: 8px;
    font-size: 11.5px; letter-spacing: 0.2px; line-height: 16px;
  }
  .categories .back-arrow, .questions .back-arrow { top: 65px; }

  /* Screen 3 – categories */
  .section-label {
    position: absolute; left: 0; right: 0;
    text-align: center; font-size: 11px; font-weight: 900; font-style: italic; letter-spacing: 0.3px;
  }
  .categories .section-label { top: 132px; }
  .category-list { position: absolute; left: 16px; right: 16px; top: 158px; display: flex; flex-direction: column; gap: 10px; }
  .category-item { height: 78px; display: flex; align-items: center; justify-content: center; font-size: 13px; font-weight: 400; }
  .view-all {
    position: absolute; left: 0; right: 0; bottom: 0; height: 58px;
    background: var(--brand-blue); color: var(--white);
    display: flex; align-items: center; justify-content: center;
    font-size: 13px; font-weight: 900; font-style: italic; letter-spacing: 0.6px;
  }

  /* Screen 4 – question list */
  .questions .app-header { height: 112px; }
  .questions .section-label { top: 128px; font-size: 12px; }
  .question-list { position: absolute; left: 14px; right: 14px; top: 156px; display: flex; flex-direction: column; gap: 10px; list-style: none; }
  .question-item { height: 70px; display: flex; align-items: center; gap: 10px; padding: 0 12px; }
  .question-number {
    flex: 0 0 30px; height: 30px; border-radius: 50%;
    background: var(--brand-blue); color: var(--white);
    display: flex; align-items: center; justify-content: center;
    font-size: 15px; font-weight: 600;
  }
  .question-text { font-size: 7.5px; line-height: 1.5; color: var(--ink-soft); }
</style>
</head>
<body>
<main class="screen-row">

  <!-- About screen -->
  <section class="screen about">
    <header class="app-header" role="img" aria-label="Header photo of an interview desk tinted in brand blue">
      <div class="status-bar"><span>9:41</span>
        <span class="status-icons"><svg width="22" height="8" viewBox="0 0 22 8"><rect x="0" y="5" width="2" height="3" fill="#fff"/><rect x="3" y="3" width="2" height="5" fill="#fff"/><rect x="6" y="1" width="2" height="7" fill="#fff"/><rect x="12" y="1" width="10" height="6" rx="1.5" fill="#fff"/></svg></span></div>
      <h1 class="app-title">Hiring Helper</h1>
    </header>
    <article class="card about-card">
      <h2>HIRING HELPER</h2>
      <p>This guide helps you prepare for common interview questions, practise clear answers and walk into every meeting feeling calm, ready and confident about the role you want.</p>
    </article>
  </section>

  <!-- Home menu screen -->
  <section class="screen home">
    <header class="app-header" role="img" aria-label="Header photo of an interview desk tinted in brand blue">
      <div class="status-bar"><span>9:41</span>
        <span class="status-icons"><svg width="22" height="8" viewBox="0 0 22 8"><rect x="0" y="5" width="2" height="3" fill="#fff"/><rect x="3" y="3" width="2" height="5" fill="#fff"/><rect x="6" y="1" width="2" height="7" fill="#fff"/><rect x="12" y="1" width="10" height="6" rx="1.5" fill="#fff"/></svg></span></div>
      <h1 class="app-title">Hiring Helper</h1>
    </header>
    <nav class="menu-list">
      <div class="card menu-item">
        <svg width="40" height="36" viewBox="0 0 40 36" fill="none" stroke="#1448c4" stroke-width="1.8" stroke-linejoin="round"><path d="M4 4h22v16H12l-6 5v-5H4z"/><path d="M26 12h10v14h-3v5l-6-5H16v-6"/><path d="M12 10a3 3 0 1 1 4 3v2M15 18v.5" stroke-linecap="round"/></svg>
        <span>View Questions &amp; Responses</span>
      </div>
      <div class="card menu-item">
        <svg width="40" height="36" viewBox="0 0 40 36" fill="none" stroke="#1448c4" stroke-width="1.8" stroke-linejoin="round"><rect x="8" y="3" width="22" height="28" rx="1"/><circle cx="19" cy="12" r="4"/><path d="M12 21h14M12 25h10"/><path d="M28 28l8-10 2 2-8 10-3 1z"/></svg>
        <span>My Question Portfolio</span>
      </div>
      <div class="card menu-item">
        <svg width="40" height="36" viewBox="0 0 40 36" fill="none" stroke="#1448c4" stroke-width="1.8" stroke-linejoin="round"><rect x="14" y="3" width="14" height="9" rx="1"/><path d="M18 12l-2 3v-3"/><path d="M4 22h32M8 22v10M32 22v10M14 22v-4h12v4"/></svg>
        <span>Interview Tips</span>
      </div>
    </nav>
  </section>

  <!-- Category screen -->
  <section class="screen categories">
    <header class="app-header" role="img" aria-label="Header photo of an interview desk tinted in brand blue">
      <div class="status-bar"><span>9:41</span>
        <span class="status-icons"><svg width="22" height="8" viewBox="0 0 22 8"><rect x="0" y="5" width="2" height="3" fill="#fff"/><rect x="3" y="3" width="2" height="5" fill="#fff"/><rect x="6" y="1" width="2" height="7" fill="#fff"/><rect x="12" y="1" width="10" height="6" rx="1.5" fill="#fff"/></svg></span></div>
      <svg class="back-arrow" width="12" height="10" viewBox="0 0 12 10" fill="none" stroke="#fff" stroke-width="1.6"><path d="M11 5H2M5 1L1 5l4 4"/></svg>
      <h1 class="app-title">View Question &amp; Responses</h1>
    </header>
    <h2 class="section-label">SELECT YOUR QUESTION CATEGORY</h2>
    <div class="category-list">
      <div class="card category-item">Behavioural</div>
      <div class="card category-item">Situational</div>
      <div class="card category-item">Motivational</div>
      <div class="card category-item">Technical</div>
    </div>
    <div class="view-all">VIEW ALL</div>
  </section>

  <!-- Question list screen -->
  <section class="screen questions">
    <header class="app-header" role="img" aria-label="Header photo of an interview desk tinted in brand blue">
      <div class="status-bar"><span>9:41</span>
        <span class="status-icons"><svg width="22" height="8" viewBox="0 0 22 8"><rect x="0" y="5" width="2" height="3" fill="#fff"/><rect x="3" y="3" width="2" height="5" fill="#fff"/><rect x="6" y="1" width="2" height="7" fill="#fff"/><rect x="12" y="1" width="10" height="6" rx="1.5" fill="#fff"/></svg></span></div>
      <svg class="back-arrow" width="12" height="10" viewBox="0 0 12 10" fill="none" stroke="#fff" stroke-width="1.6"><path d="M11 5H2M5 1L1 5l4 4"/></svg>
      <h1 class="app-title">View Question &amp; Responses</h1>
    </header>
    <h2 class="section-label">BEHAVIOURAL</h2>
    <ol class="question-list">
      <li class="card question-item"><span class="question-number">1</span><p class="question-text">Tell us about a time you solved a problem at work. Describe the situation, your actions and the result you achieved.</p></li>
      <li class="card question-item"><span class="question-number">2</span><p class="question-text">Share an example of working in a team under pressure. Explain your role, how you helped others and what you learned.</p></li>
      <li class="card question-item"><span class="question-number">3</span><p class="question-text">Describe a moment you handled a difficult customer. Focus on listening, staying calm and finding a fair outcome for both.</p></li>
      <li class="card question-item"><span class="question-number">4</span><p class="question-text">Give an example of a goal you set and reached. Outline the steps you planned and how you tracked your progress.</p></li>
      <li class="card question-item"><span class="question-number">5</span><p class="question-text">Talk about a mistake you made and fixed. Show what went wrong, how you owned it and what changed afterwards.</p></li>
    </ol>
  </section>

</main>
</body>
</html>
```